Business Card Design

We are a residential half way house for the addict ,the alcoholic and dual diagnosed in recovery.
i house both men and woman age 18+

Industry/Entity Type

Residential

```html
<!DOCTYPE html>
<html lang="en">
<head>
<meta charset="utf-8">
<title>Harmony's Family Sober House – Business Card</title>
<link rel="stylesheet" href="https://fonts.googleapis.com/css2?family=Anton&family=Open+Sans:wght@400&family=Roboto:wght@400&display=swap">
<style>
  :root {
    --page-bg: #e7e4df;
    --card-top: #ffffff;
    --card-bottom: #d9d9d9;
    --brand-red: #d7002a;
    --ink: #111111;
    --stripe-light: #c9c9c9;
    --stripe-dark: #a8a8a8;
    --contact-ink: #1c1c1c;
  }
  * { margin: 0; padding: 0; box-sizing: border-box; }
  html, body {
    width: 1200px; height: 892px; overflow: hidden;
    background: var(--page-bg);
  }
  .card {
    position: absolute; left: 410px; top: 113px;
    width: 380px; height: 665px;
    background: linear-gradient(180deg, var(--card-top) 0%, #f4f4f4 45%, var(--card-bottom) 100%);
    box-shadow: 0 6px 18px rgba(0,0,0,0.18);
    overflow: hidden;
  }
  .accent-band {
    position: absolute; left: 0; top: 0;
    width: 38px; height: 379px;
    background: var(--brand-red);
  }
  .accent-square {
    position: absolute; background: var(--brand-red);
  }
  .accent-square--top { right: 0; top: 66px; width: 38px; height: 58px; }
  .accent-square--bottom { left: 0; top: 600px; width: 40px; height: 42px; }

  .holder {
    position: absolute; right: 50px; top: 76px; text-align: right;
    font-family: 'Open Sans', sans-serif; color: var(--ink);
  }
  .holder__name { font-size: 27px; line-height: 1.1; letter-spacing: 0.3px; }
  .holder__role { font-size: 11px; line-height: 1.3; }
  .holder__note { font-size: 11px; line-height: 1.2; }

  .company {
    position: absolute; left: 46px; top: 282px;
    font-family: 'Anton', sans-serif; color: var(--ink);
    line-height: 1;
  }
  .company__lead { font-size: 44px; letter-spacing: 0.5px; }
  .company__rest { font-size: 29px; margin-top: 2px; letter-spacing: 0.2px; }

  .contacts {
    position: absolute; left: 0; top: 379px; list-style: none;
  }
  .contacts__item {
    display: flex; align-items: center;
    width: 353px; height: 44px; margin-bottom: 7px;
    padding-left: 50px;
    background: linear-gradient(180deg, var(--stripe-light), var(--stripe-dark));
    font-family: 'Roboto', sans-serif; font-size: 15px; color: var(--contact-ink);
  }
  .contacts__icon { width: 15px; height: 15px; margin-right: 12px; flex: none; fill: var(--brand-red); }
</style>
</head>
<body>
  <main class="card">
    <div class="accent-band"></div>
    <div class="accent-square accent-square--top"></div>

    <div class="holder">
      <p class="holder__name">Dana Whitfield</p>
      <p class="holder__role">Owner</p>
      <p class="holder__note">(15 yrs.in recovery)</p>
    </div>

    <div class="company">
      <p class="company__lead">Harmony's</p>
      <p class="company__rest">Family Sober House Inc</p>
    </div>

    <ul class="contacts">
      <li class="contacts__item">
        <svg class="contacts__icon" viewBox="0 0 24 24"><path d="M6.6 10.8a15 15 0 0 0 6.6 6.6l2.2-2.2c.3-.3.7-.4 1-.2 1.1.4 2.3.6 3.6.6.6 0 1 .4 1 1V20c0 .6-.4 1-1 1A17 17 0 0 1 3 4c0-.6.4-1 1-1h3.5c.6 0 1 .4 1 1 0 1.3.2 2.5.6 3.6.1.3 0 .7-.2 1z"/></svg>
        (555) 014-0305
      </li>
      <li class="contacts__item">
        <svg class="contacts__icon" viewBox="0 0 24 24"><path d="M6.6 10.8a15 15 0 0 0 6.6 6.6l2.2-2.2c.3-.3.7-.4 1-.2 1.1.4 2.3.6 3.6.6.6 0 1 .4 1 1V20c0 .6-.4 1-1 1A17 17 0 0 1 3 4c0-.6.4-1 1-1h3.5c.6 0 1 .4 1 1 0 1.3.2 2.5.6 3.6.1.3 0 .7-.2 1z"/></svg>
        (555) 014-0306
      </li>
      <li class="contacts__item">
        <svg class="contacts__icon" viewBox="0 0 24 24"><path d="M6 2h10l2 2v5H6z M3 10h18v8h-3v4H6v-4H3z M8 15v5h8v-5z"/></svg>
        (555) 014-5536
      </li>
      <li class="contacts__item">
        <svg class="contacts__icon" viewBox="0 0 24 24"><path d="M2 5h20v14H2z M2 5l10 8 10-8" stroke="#c9c9c9" stroke-width="1.5"/></svg>
        danawhitfield@example.com
      </li>
      <li class="contacts__item">
        <svg class="contacts__icon" viewBox="0 0 24 24"><path d="M12 2a7 7 0 0 0-7 7c0 5 7 13 7 13s7-8 7-13a7 7 0 0 0-7-7zm0 9.5a2.5 2.5 0 1 1 0-5 2.5 2.5 0 0 1 0 5z"/></svg>
        4721 Palm Crest Rd. Bayside,Fla 33000
      </li>
    </ul>

    <div class="accent-square accent-square--bottom"></div>
  </main>
</body>
</html>
```